Redesign of business card for Cedar Ridge Mechanical

We are looking for a new design for our business cards for Cedar Ridge Mechanical. We are a plumbing & HVAC construction company, operating on the West Coast of Canada and USA. Logo attached.
Industry/Entity Type
Construction - Plumbing & HVAC
Contact Information for Business Card
Name, address, phone numbers, email, website address
Look and feel
Each slider illustrates characteristics of the customer's brand and the style your logo design should communicate.

```html
<!DOCTYPE html>
<html lang="en">
<head>
<meta charset="utf-8">
<title>Cedar Ridge Mechanical — Business Card</title>
<link href="https://fonts.googleapis.com/css2?family=Arimo:wght@400;700&display=swap" rel="stylesheet">
<style>
  :root {
    --backdrop: #d9d9d9;
    --card-light: #ffffff;
    --card-dark: #2f2f2f;
    --ink: #111111;
    --ink-soft: #444444;
    --ink-muted: #777777;
    --mark-dark: #5a5a5a;
  }
  * { box-sizing: border-box; margin: 0; padding: 0; }
  html, body { width: 1200px; height: 800px; overflow: hidden; }
  body {
    background: var(--backdrop);
    font-family: "Arimo", Arial, sans-serif;
    display: flex;
    align-items: center;
    justify-content: center;
    gap: 60px;
  }
  .card {
    width: 525px;
    height: 300px;
    border-radius: 22px;
    position: relative;
    overflow: hidden;
  }
  .card-front { background: var(--card-light); color: var(--ink); }
  .card-back { background: var(--card-dark); }

  .front-brand {
    position: absolute;
    top: 34px;
    right: 34px;
    display: flex;
    align-items: center;
    gap: 14px;
  }
  .brand-square {
    width: 34px;
    height: 34px;
    background: var(--ink);
  }
  .brand-name {
    font-weight: 700;
    font-size: 22px;
    letter-spacing: 0.02em;
    color: var(--ink);
  }

  .identity {
    position: absolute;
    left: 34px;
    top: 120px;
  }
  .identity .person {
    font-weight: 700;
    font-size: 19px;
    color: var(--ink);
  }
  .identity .role {
    font-size: 14px;
    color: var(--ink-muted);
    margin-top: 2px;
  }

  .contact {
    position: absolute;
    left: 34px;
    bottom: 28px;
    font-size: 13.5px;
    line-height: 1.35;
    color: var(--ink-soft);
  }
  .contact .address { margin-bottom: 10px; }
  .contact .line { display: flex; align-items: center; gap: 8px; }
  .contact svg { width: 11px; height: 11px; flex: none; }

  .back-brand {
    position: absolute;
    inset: 0;
    display: flex;
    align-items: center;
    justify-content: center;
    gap: 16px;
  }
  .back-brand .brand-square { background: var(--mark-dark); width: 40px; height: 40px; }
  .back-brand .brand-name {
    color: var(--mark-dark);
    font-size: 24px;
    text-transform: uppercase;
    letter-spacing: 0.08em;
  }
</style>
</head>
<body>
  <section class="card card-front">
    <div class="front-brand">
      <span class="brand-square"></span>
      <span class="brand-name">Cedar Ridge Mechanical</span>
    </div>

    <div class="identity">
      <p class="person">Owen Hartley</p>
      <p class="role">President</p>
    </div>

    <div class="contact">
      <p class="address">2176 Alder Grove Lane<br>Port Moody, BC V3H 1K2</p>
      <p class="line">
        <svg viewBox="0 0 12 12" aria-hidden="true"><path d="M2.5 1h2l1 3-1.3 1a6 6 0 0 0 2.8 2.8l1-1.3 3 1v2a1 1 0 0 1-1 1A9.5 9.5 0 0 1 1.5 2a1 1 0 0 1 1-1z" fill="#111"/></svg>
        (604) 5128-3390
      </p>
      <p class="line">
        <svg viewBox="0 0 12 12" aria-hidden="true"><rect x="0.5" y="2" width="11" height="8" fill="#111"/><path d="M0.5 2.5 6 6.5l5.5-4" stroke="#fff" stroke-width="1" fill="none"/></svg>
        name@cedarridgemechanical.com
      </p>
      <p class="line">
        <svg viewBox="0 0 12 12" aria-hidden="true"><circle cx="6" cy="6" r="5.5" fill="#111"/><path d="M3.5 6h5M6 3.5v5" stroke="#fff" stroke-width="1"/></svg>
        www.cedarridgemechanical.com
      </p>
    </div>
  </section>

  <section class="card card-back">
    <div class="back-brand">
      <span class="brand-square"></span>
      <span class="brand-name">Cedar Ridge Mechanical</span>
    </div>
  </section>
</body>
</html>
```